Business Card Design - ChoiceCraft

Looking for creative, modern design, two sided for ChoiceCraft that is consistent with color and feel of website www.choicecraftpro.net.
Updates

Back of card will be used to promote products or have a quote revolving around decisions, change, leadership, innovation, creativity. Back should also have space to promote website, but optional to use the icon. Front of the card will need to use the icon and have standard place for name, job title, phone and email. We are not looking to put a mailing address or fax. Also want space to place a few words/phrase explaining what we do...such as individual growth and organizational development or tools, training, information...in addition, want the facebook icon small on the front somewhere as we are also on facebook.

Vector file uploaded of icon.

Target Market(s)

Professional coaching for individual growth and organizational development

Industry/Entity Type

Business

Requirements
Must have
• Icon...see attached.

```html
<!DOCTYPE html>
<html lang="en">
<head>
<meta charset="utf-8">
<title>ChoiceCraft Business Card</title>
<link rel="stylesheet" href="https://fonts.googleapis.com/css2?family=Arimo:wght@400;700&display=swap">
<style>
  :root {
    --bg: #d9dadc;
    --card: #ffffff;
    --card-edge: #3a3a3a;
    --ink: #1d1d1d;
    --ink-soft: #3b3b3b;
    --grey: #555555;
    --divider: #c9c9c9;
    --navy: #2e3f8c;
    --sky: #4fb0e0;
    --brand-blue: #2e8fc8;
    --mark-blue: #3f86cf;
    --faint: #eaf1f8;
  }
  * { margin: 0; padding: 0; box-sizing: border-box; }
  html, body { width: 1200px; height: 1069px; overflow: hidden; }
  body {
    background: var(--bg);
    font-family: "Arimo", Arial, sans-serif;
    color: var(--ink);
    position: relative;
  }
  .card {
    position: absolute;
    background: var(--card);
    border: 1.5px solid var(--card-edge);
    border-radius: 29px;
    overflow: hidden;
  }
  .card--front { left: 88px; top: 76px; width: 763px; height: 435px; }
  .card--back { left: 355px; top: 569px; width: 759px; height: 432px; }

  /* Front */
  .brand-mark {
    position: absolute; left: 132px; top: 60px;
    width: 164px; height: 164px; border-radius: 50%;
    background: var(--mark-blue);
  }
  .brand-name {
    position: absolute; left: 89px; top: 258px;
    font-size: 33px; font-weight: 700; color: var(--ink);
    letter-spacing: 0.5px;
  }
  .front-divider {
    position: absolute; left: 382px; top: 114px;
    width: 1px; height: 192px; background: var(--divider);
  }
  .person {
    position: absolute; left: 408px; top: 136px;
    font-size: 25px; font-weight: 700; color: var(--ink);
  }
  .person .title { font-size: 19px; font-weight: 400; color: var(--ink-soft); }
  .contacts {
    position: absolute; left: 412px; top: 188px;
    list-style: none;
  }
  .contacts li {
    display: flex; align-items: center; gap: 9px;
    height: 26.5px; font-size: 20px; color: var(--ink-soft);
  }
  .contacts svg { width: 14px; height: 14px; flex: none; }
  .band-navy {
    position: absolute; left: 0; top: 356px;
    width: 33px; height: 5px; background: var(--navy);
  }
  .band-sky {
    position: absolute; left: 43px; top: 356px;
    right: 0; height: 5px; background: var(--sky);
  }
  .tagline {
    position: absolute; left: 62px; top: 386px;
    font-size: 19px; color: var(--grey);
  }

  /* Back */
  .back-backdrop {
    position: absolute; left: 300px; top: 60px;
    width: 310px; height: 310px; border-radius: 50%;
    background: var(--faint);
  }
  .quotes { position: absolute; left: 26px; top: 32px; list-style: none; }
  .quote { position: relative; height: 77.5px; padding-left: 70px; }
  .quote__dot {
    position: absolute; left: 2px; top: 6px;
    width: 30px; height: 30px; border-radius: 50%;
    background: var(--mark-blue);
  }
  .quote__text {
    font-size: 19px; color: var(--ink-soft); position: relative; white-space: nowrap;
  }
  .quote__text::before {
    content: "\201C"; position: absolute; left: -27px; top: -10px;
    font-size: 34px; font-weight: 700; color: var(--ink-soft);
  }
  .quote__text::after {
    content: "\201D"; font-size: 34px; font-weight: 700; color: var(--ink-soft);
    line-height: 0; position: relative; top: 14px; margin-left: 2px;
  }
  .quote__author {
    font-size: 19px; font-weight: 700; color: var(--brand-blue); margin-top: 2px;
  }
</style>
</head>
<body>

<section class="card card--front" aria-label="Card front">
  <div class="brand-mark"></div>
  <div class="brand-name">ChoiceCraft</div>
  <div class="front-divider"></div>
  <div class="person">Your Name, <span class="title">Title</span></div>
  <ul class="contacts">
    <li>
      <svg viewBox="0 0 14 14" aria-hidden="true"><circle cx="7" cy="7" r="6" fill="none" stroke="#333" stroke-width="1.2"/><path d="M4.5 4 L6 3.6 L6.6 5.6 L5.7 6.3 Q6.6 8 7.8 8.6 L8.6 7.8 L10.4 8.5 L10 10 Q6.5 10 4.5 4 Z" fill="#333"/></svg>
      123-456-789
    </li>
    <li>
      <svg viewBox="0 0 14 14" aria-hidden="true"><rect x="1" y="3" width="12" height="8.5" fill="#333"/><path d="M1.5 3.5 L7 8 L12.5 3.5" fill="none" stroke="#fff" stroke-width="1"/></svg>
      info@choicecraftpro.net
    </li>
    <li>
      <svg viewBox="0 0 14 14" aria-hidden="true"><circle cx="7" cy="7" r="6" fill="none" stroke="#333" stroke-width="1.2"/><ellipse cx="7" cy="7" rx="2.6" ry="6" fill="none" stroke="#333" stroke-width="1"/><path d="M1 7 H13 M2 4 H12 M2 10 H12" stroke="#333" stroke-width="0.9"/></svg>
      www.choicecraftpro.net
    </li>
    <li>
      <svg viewBox="0 0 14 14" aria-hidden="true"><rect x="1.5" y="1.5" width="11" height="11" rx="1.5" fill="#3b5a9a"/></svg>
      /choicecraftpro
    </li>
  </ul>
  <div class="band-navy"></div>
  <div class="band-sky"></div>
  <p class="tagline">Supporting individual growth and&nbsp; organizational development.</p>
</section>

<section class="card card--back" aria-label="Card back">
  <div class="back-backdrop"></div>
  <ul class="quotes">
    <li class="quote"><span class="quote__dot"></span>
      <div class="quote__text">Try not to become a man of success, but rather a man of value.</div>
      <div class="quote__author">- Alden Everhart</div></li>
    <li class="quote"><span class="quote__dot"></span>
      <div class="quote__text">The only constant is change.</div>
      <div class="quote__author">- Helion Carter</div></li>
    <li class="quote"><span class="quote__dot"></span>
      <div class="quote__text">We are what we repeatedly do. Excellence is not an act, it is a habit.</div>
      <div class="quote__author">- Arista Tolland</div></li>
    <li class="quote"><span class="quote__dot"></span>
      <div class="quote__text">Simplicity is the ultimate sophistication.</div>
      <div class="quote__author">- Leona Davies</div></li>
    <li class="quote"><span class="quote__dot"></span>
      <div class="quote__text">Life is not fair - get used to it.</div>
      <div class="quote__author">- Bill Garrow</div></li>
  </ul>
</section>

</body>
</html>
```